Meadow Kr Circle (company name is Meadow Kr Circle LLP)

management of homestay, hospitality something similar with https://www.dorvika.example

Target Market(s)

johor bahru market (Malaysia)

Contact Information for Business Card

Meadow Circle KR LLP

Logo Text

eyes catching, attractive, amazing, Nice, jaw dropping for design

Coding

Coded - Design and coding required

Number of Pages Required

5+ page

Colors

Designer to choose colors to be used in the design.

Requirements
Must have
• please change the short term proposal to our company logo and change the name from dorvika to meadow KR Circle LLP
• thanks
Nice to have
• please let me have eyes catching , jaw dropping design

```html
<!DOCTYPE html>
<html lang="en">
<head>
<meta charset="utf-8">
<title>Meadow Kr Circle – Homestay Management</title>
<link href="https://fonts.googleapis.com/css2?family=Poppins:ital,wght@0,400;0,500;0,600;0,700;1,400;1,600;1,700&display=swap" rel="stylesheet">
<style>
:root{
  --green:#0b8a0b;
  --green-dark:#066a06;
  --blue:#1d84c6;
  --ink:#1e1e1e;
  --muted:#555;
  --light:#f1f1f1;
  --dark:#111;
  --white:#fff;
  --star:#f39c12;
}
*{box-sizing:border-box;margin:0;padding:0}
html,body{width:1200px;height:4358px;overflow:hidden}
body{font-family:"Poppins",sans-serif;color:var(--ink);background:var(--white);position:relative}
section,header,footer{position:absolute;left:0;width:1200px}
.abs{position:absolute}

/* header */
.site-header{top:0;height:220px;border-bottom:6px solid var(--green)}
.header-address{left:100px;top:36px;width:260px;font-size:15px;line-height:26px;color:#333;padding-left:36px}
.header-address svg{position:absolute;left:0;top:4px}
.brand{left:0;width:1200px;top:28px;text-align:center;font-size:52px;font-weight:700;color:var(--ink)}
.header-phone{right:100px;top:56px;font-size:15px;color:#333;padding-left:34px}
.header-phone svg{position:absolute;left:0;top:0}
.main-nav{top:150px;left:0;width:1200px;display:flex;justify-content:center;gap:42px;font-size:17px;font-weight:500}
.main-nav span{color:#222}

/* hero */
.hero{top:226px;height:800px}
.hero-photo{left:0;top:0;width:1200px;height:620px;background:linear-gradient(135deg,#7c8a8e,#4e5860 45%,#8f8373 75%,#5c6266)}
.hero-shade{left:0;top:0;width:1200px;height:620px;background:rgba(20,25,30,.35)}
.hero-title{top:228px;width:1200px;text-align:center;color:#fff;font-size:56px;font-weight:700}
.hero-sub{top:300px;left:200px;width:800px;text-align:center;color:#fff;font-size:18px;line-height:28px}
.btn{display:inline-block;background:var(--blue);color:#fff;text-align:center;font-weight:500}
.hero-btn{top:384px;left:480px;width:238px;height:56px;line-height:56px;font-size:24px}
.hero-curve{left:0;top:440px}
.service{top:536px;width:270px;height:276px;background:var(--green);color:#fff;text-align:center;padding:32px 22px 0}
.service.is-blue{background:var(--blue)}
.service h3{font-size:17px;font-weight:700;line-height:21px;margin-top:12px}
.service p{font-size:13px;line-height:18px;margin-top:12px}

/* about */
.about{top:1110px;height:420px}
.about-frame{left:87px;top:5px;width:518px;height:390px;background:linear-gradient(135deg,#e9ecee,#c3c8cc 50%,#9aa3aa);}
.about-inner{left:25px;top:25px;width:468px;height:340px;border:2px solid #fff}
.about h2{left:625px;top:15px;font-size:38px;font-weight:700}
.about-text{left:625px;top:95px;width:480px;font-size:15px;line-height:33px;color:#333}
.about-btn{left:625px;top:340px;width:200px;height:56px;line-height:56px;font-size:23px}

/* steps */
.steps{top:1575px;height:445px}
.steps-bg{left:0;top:0;width:1200px;height:445px;background:linear-gradient(120deg,#3f454a,#6c737a 50%,#2c3136)}
.steps-shade{left:0;top:0;width:1200px;height:445px;background:rgba(0,0,0,.4)}
.section-title{width:1200px;text-align:center;font-size:38px;font-weight:700}
.steps .section-title{top:50px;color:#fff;font-size:34px}
.step{top:148px;width:221px;height:235px}
.step svg{position:absolute;left:0;top:0}
.step-num{position:absolute;top:18px;width:221px;text-align:center;font-size:36px;font-weight:700;color:#fff}
.step-label{position:absolute;top:115px;left:20px;width:181px;text-align:center;font-size:16px;line-height:22px;color:#222}

/* packages */
.packages{top:2040px;height:850px}
.packages .section-title{top:20px;font-size:38px}
.packages .subtitle{top:85px;width:1200px;text-align:center;font-size:26px;font-weight:600}
.pkg{top:175px;width:298px;height:508px;background:#fff;border-radius:26px;box-shadow:0 6px 18px rgba(0,0,0,.25);padding:38px 20px 0;text-align:center}
.pkg.is-featured{background:var(--green);color:#fff}
.pkg h3{font-size:22px;font-weight:700;margin-top:10px;white-space:nowrap}
.pkg ul{list-style:none;text-align:left;margin-top:22px;padding-left:20px}
.pkg li{font-size:12px;line-height:40px;position:relative;padding-left:22px;white-space:nowrap}
.pkg.is-featured li{line-height:28px}
.pkg.is-electrical li{line-height:31px}
.pkg li::before{content:"";position:absolute;left:0;top:50%;width:10px;height:5px;border-left:2px solid currentColor;border-bottom:2px solid currentColor;transform:translateY(-70%) rotate(-45deg)}
.price{position:absolute;bottom:34px;left:56px;display:flex;gap:26px}
.price .paid{background:var(--green);color:#fff;width:70px;height:24px;line-height:24px;font-size:12px;text-align:center}
.pkg.is-featured .price .paid{background:#fff;color:var(--green)}
.price .amount{background:#fff;color:#222;border:1px solid #ccc;width:84px;height:24px;line-height:24px;font-size:12px;text-align:center}
.pkg-btn{top:755px;left:480px;width:238px;height:54px;line-height:54px;font-size:17px}

/* testimonials */
.testimonials{top:2897px;height:432px;background:var(--light)}
.testimonials .section-title{top:42px;font-size:38px}
.quote{top:168px;width:340px}
.avatar{top:165px;width:120px;height:120px;border-radius:50%;border:4px solid #fff;box-shadow:0 2px 8px rgba(0,0,0,.2)}
.quote p{font-size:15px;line-height:26px;font-style:italic;color:#333;padding:8px 0 0 14px;position:relative}
.quote p::before{content:"\201C";position:absolute;left:-4px;top:-10px;font-size:40px;font-style:normal;font-weight:700}
.quote .closing{font-size:36px;font-weight:700;font-style:normal;line-height:0;vertical-align:-12px}
.quote .who{font-size:16px;font-weight:700;font-style:italic;margin-top:16px}
.stars{display:flex;gap:4px;margin-top:6px}

/* blog */
.blog{top:3333px;height:561px}
.blog-bg{left:0;top:0;width:1200px;height:561px;background:linear-gradient(120deg,#2f3438,#5d646a 50%,#262a2e)}
.blog-shade{left:0;top:0;width:1200px;height:561px;background:rgba(0,0,0,.45)}
.blog .section-title{top:55px;color:#fff;font-size:38px}
.post{top:143px;height:340px;background:#fff;text-align:center}
.post-img{width:100%;height:145px}
.post-meta{font-size:13px;color:#333;margin-top:12px;word-spacing:30px}
.post h3{font-size:22px;font-weight:700;margin-top:2px}
.post p{font-size:14px;line-height:25px;color:#333;padding:6px 22px 0}
.post-wide{left:610px;width:497px}
.post-wide .post-img{position:absolute;left:0;top:0;width:250px;height:340px}
.post-wide .post-body{position:absolute;left:262px;top:14px;width:228px}
.arrow{top:320px;width:46px;height:46px;border-radius:50%;background:#fff}
.arrow svg{position:absolute;left:13px;top:13px}

/* footer */
.site-footer{top:3894px;height:464px;background:var(--dark);color:#fff}
.footer-brand{left:130px;top:125px;font-size:42px;font-weight:700}
.footer-about{left:130px;top:205px;width:420px;font-size:15px;line-height:29px}
.footer-col h4{font-size:17px;font-weight:700;letter-spacing:1px}
.footer-links{left:593px;top:80px}
.footer-links ul{list-style:none;margin-top:28px}
.footer-links li{font-size:14px;line-height:32.5px}
.footer-contact{left:770px;top:80px}
.contact-row{position:relative;padding-left:40px;font-size:15px;line-height:30px;margin-top:6px}
.contact-row svg{position:absolute;left:0;top:8px}
.footer-contact .first{margin-top:24px}
.copyright{left:90px;top:408px;font-size:14px}
.social{top:396px;left:935px;display:flex;gap:14px}
.social span{width:34px;height:34px;border:2px solid #fff;border-radius:50%}
</style>
</head>
<body>

<header class="site-header">
  <div class="abs header-address">
    <svg width="20" height="26" viewBox="0 0 20 26"><path d="M10 1a8 8 0 0 0-8 8c0 6 8 15 8 15s8-9 8-15a8 8 0 0 0-8-8z" fill="none" stroke="#333" stroke-width="1.8"/><circle cx="10" cy="9" r="3" fill="none" stroke="#333" stroke-width="1.8"/></svg>
    Unit 12-03 Riverlane Tower, Jalan Seruni, Taman Kenari, 81200
  </div>
  <div class="abs brand">Meadow Kr Circle</div>
  <div class="abs header-phone">
    <svg width="22" height="22" viewBox="0 0 24 24"><path d="M5 3h4l2 5-3 2a12 12 0 0 0 6 6l2-3 5 2v4a2 2 0 0 1-2 2A18 18 0 0 1 3 5a2 2 0 0 1 2-2z" fill="none" stroke="#333" stroke-width="1.6"/></svg>
    +60 7 555 0182
  </div>
  <nav class="abs main-nav">
    <span>Home</span><span>About Us</span><span>How To Start?</span><span>Package</span><span>Blog</span><span>Testimonial</span><span>Contact Us</span>
  </nav>
</header>

<section class="hero">
  <div class="abs hero-photo" role="img" aria-label="Photo of a team meeting around a table in a bright office"></div>
  <div class="abs hero-shade"></div>
  <h1 class="abs hero-title">Welcome To Meadow Kr Circle.</h1>
  <p class="abs hero-sub">It is a long established fact that a reader will be distracted by the readable content of a page when looking at its layout.</p>
  <span class="abs btn hero-btn">View More</span>
  <svg class="abs hero-curve" width="1200" height="360" viewBox="0 0 1200 360">
    <path d="M0 100 Q600 230 1200 150 L1200 360 L0 360 Z" fill="#fff"/>
    <path d="M0 100 Q600 230 1200 150" fill="none" stroke="var(--green)" stroke-width="10"/>
  </svg>
  <div class="abs service" style="left:203px">
    <svg width="60" height="66" viewBox="0 0 60 66" fill="none" stroke="#fff" stroke-width="2.5"><rect x="14" y="4" width="30" height="56"/><path d="M44 4l-14 8v52"/><circle cx="35" cy="34" r="2" fill="#fff"/><path d="M4 34h14M12 28l6 6-6 6"/></svg>
    <h3>Answering Enquirers, Check-Ins / Outs</h3>
    <p>We will answer all guest's enquiries ,meet them to handover key and verification check.We also provide 24hr on-call support.</p>
  </div>
  <div class="abs service is-blue" style="left:488px">
    <svg width="90" height="66" viewBox="0 0 90 66" fill="none" stroke="#fff" stroke-width="2.5"><rect x="8" y="20" width="46" height="30"/><path d="M54 28h14l12 12v10H54z"/><circle cx="22" cy="54" r="6"/><circle cx="68" cy="54" r="6"/><path d="M20 6l4 8M34 4v10M48 6l-4 8"/></svg>
    <h3>Cleaning, Laundry and Maintenance</h3>
    <p>We get the professional cleaning team to clean up the place after the guest checked-out every time.</p>
  </div>
  <div class="abs service" style="left:776px">
    <svg width="66" height="66" viewBox="0 0 66 66" fill="none" stroke="#fff" stroke-width="3"><path d="M6 32L33 8l27 24"/><path d="M14 26v32h38V26"/><rect x="27" y="40" width="12" height="18"/></svg>
    <h3>Marketing &amp; Optimization</h3>
    <p>We take professional photos and write persuasive copywriting to optimize your listing in order to get more booking.</p>
  </div>
</section>

<section class="about">
  <div class="abs about-frame" role="img" aria-label="Photo of a presenter pointing at a chart in front of a seated team">
    <div class="abs about-inner"></div>
  </div>
  <h2 class="abs">About us</h2>
  <p class="abs about-text">We are a short-term rental management and provides hospitality services to help property owners maximise their rental income. Our goal is to help you reap the most from your rental income without you having to do any of the hard work such as handle all the particular renting problems on StayNest, RoomHarbor, cleaning and dealing with tenants and guests.</p>
  <span class="abs btn about-btn">Read More</span>
</section>

<section class="steps">
  <div class="abs steps-bg" role="img" aria-label="Background photo of a business meeting"></div>
  <div class="abs steps-shade"></div>
  <h2 class="abs section-title">How to start?</h2>
  <div class="abs step" style="left:122px">
    <svg width="221" height="235" viewBox="0 0 221 235"><polygon points="0,45 110,0 221,45 221,180 110,235 0,180" fill="#fff"/><polygon points="0,45 110,0 221,45 221,58 0,58" fill="var(--green)"/></svg>
    <div class="step-num">01</div><div class="step-label">Getting the required items</div>
  </div>
  <div class="abs step" style="left:372px">
    <svg width="221" height="235" viewBox="0 0 221 235"><polygon points="0,45 110,0 221,45 221,180 110,235 0,180" fill="#fff"/><polygon points="0,45 110,0 221,45 221,58 0,58" fill="var(--green)"/></svg>
    <div class="step-num">02</div><div class="step-label">Renovation &amp; Furnishing</div>
  </div>
  <div class="abs step" style="left:625px">
    <svg width="221" height="235" viewBox="0 0 221 235"><polygon points="0,45 110,0 221,45 221,180 110,235 0,180" fill="#fff"/><polygon points="0,45 110,0 221,45 221,58 0,58" fill="var(--green)"/></svg>
    <div class="step-num">03</div><div class="step-label">Sign a management agreement</div>
  </div>
  <div class="abs step" style="left:878px">
    <svg width="221" height="235" viewBox="0 0 221 235"><polygon points="0,45 110,0 221,45 221,180 110,235 0,180" fill="#fff"/><polygon points="0,45 110,0 221,45 221,58 0,58" fill="var(--green)"/></svg>
    <div class="step-num">04</div><div class="step-label">Handover Keys &amp; Access cards, and relevant information</div>
  </div>
</section>

<section class="packages">
  <h2 class="abs section-title">Package</h2>
  <div class="abs subtitle">Renovation &amp; Furnishing</div>
  <div class="abs pkg" style="left:96px">
    <svg width="52" height="52" viewBox="0 0 52 52"><rect x="6" y="20" width="40" height="28" fill="#f5a623"/><rect x="3" y="14" width="46" height="9" fill="#e8412c"/><rect x="23" y="14" width="6" height="34" fill="#e8412c"/><path d="M26 14c-6-10-16-6-10 0M26 14c6-10 16-6 10 0" fill="none" stroke="#e8412c" stroke-width="3"/></svg>
    <h3>Economic Package</h3>
    <ul>
      <li>Full Height Day &amp; Night curtain</li>
      <li>Main Entrance Door Grill</li>
      <li>Supply &amp; Install LED Surface Light</li>
      <li>Supply &amp; Install Down Light</li>
      <li>Supply &amp; Install Ceiling Fan</li>
      <li>Retractive Hanging Rack</li>
    </ul>
    <div class="price"><span class="paid">Paid</span><span class="amount">RM1,550.00</span></div>
  </div>
  <div class="abs pkg is-featured" style="left:445px">
    <svg width="70" height="52" viewBox="0 0 70 52" fill="none" stroke="#fff" stroke-width="2.5"><rect x="14" y="20" width="42" height="6"/><path d="M18 26v22M52 26v22"/><path d="M2 10v38M2 30h10v18M68 10v38M68 30H58v18"/><path d="M30 20V6h10v14"/></svg>
    <h3>Furniture Package</h3>
    <ul>
      <li>Sofa bed</li><li>Coffee table</li><li>Dining table set with 6-seaters</li><li>Queen mattress with divan</li><li>Microfiber pillows</li><li>Carpet rug</li><li>Study table &amp; chairs</li><li>Ironing board</li><li>Bedside tables</li>
    </ul>
    <div class="price"><span class="paid">Paid</span><span class="amount">RM1,900.00</span></div>
  </div>
  <div class="abs pkg is-electrical" style="left:796px">
    <svg width="52" height="52" viewBox="0 0 52 52"><circle cx="26" cy="22" r="12" fill="#f5c518"/><rect x="20" y="34" width="12" height="10" fill="#777"/><path d="M26 2v4M8 10l3 3M44 10l-3 3M4 24h4M44 24h4" stroke="#f5a623" stroke-width="2.5"/></svg>
    <h3>Electrical Appliances</h3>
    <ul>
      <li>50" LED Smart TV</li><li>2 door fridge</li><li>7kg washing machine</li><li>Steam Iron</li><li>Electric Kettle</li><li>Hair dryer</li><li>Bread toaster</li><li>Water filter</li>
    </ul>
    <div class="price"><span class="paid">Paid</span><span class="amount">RM6,000.00</span></div>
  </div>
  <span class="abs btn pkg-btn">View More Packages</span>
</section>

<section class="testimonials">
  <h2 class="abs section-title">Testimonials</h2>
  <div class="abs avatar" style="left:105px;background:linear-gradient(160deg,#e8e2da,#b9a797)" role="img" aria-label="Portrait of a satisfied property owner"></div>
  <div class="abs quote" style="left:240px">
    <p>Lorem Ipsum is simply dummy text of the printing and typesetting industry. Lorem Ipsum has been the industry's standard dummy text ever since the 1500s. <span class="closing">&#8221;</span></p>
    <div class="who">Dana Ruel, Kuala Lumpur</div>
    <div class="stars">
      <svg width="110" height="20" viewBox="0 0 110 20" fill="var(--star)"><polygon id="s1" points="10,0 13,7 20,7 14,12 16,20 10,15 4,20 6,12 0,7 7,7"/><use href="#s1" x="22"/><use href="#s1" x="44"/><use href="#s1" x="66"/><use href="#s1" x="88"/></svg>
    </div>
  </div>
  <div class="abs quote" style="left:625px">
    <p>Lorem Ipsum is simply dummy text of the printing and typesetting industry. Lorem Ipsum has been the industry's standard dummy text ever since the 1500s. <span class="closing">&#8221;</span></p>
    <div class="who">Oren Vale, Singapore</div>
    <div class="stars">
      <svg width="110" height="20" viewBox="0 0 110 20" fill="var(--star)"><use href="#s1"/><use href="#s1" x="22"/><use href="#s1" x="44"/><use href="#s1" x="66"/><use href="#s1" x="88"/></svg>
    </div>
  </div>
  <div class="abs avatar" style="left:975px;background:linear-gradient(160deg,#cfd6dc,#8c969e)" role="img" aria-label="Portrait of a happy guest"></div>
</section>

<section class="blog">
  <div class="abs blog-bg" role="img" aria-label="Background photo of a workspace"></div>
  <div class="abs blog-shade"></div>
  <h2 class="abs section-title">Blog</h2>
  <div class="abs arrow" style="left:21px"><svg width="20" height="20" viewBox="0 0 20 20"><path d="M13 3L6 10l7 7" fill="none" stroke="#111" stroke-width="3"/></svg></div>
  <article class="abs post" style="left:96px;width:241px">
    <div class="post-img" role="img" aria-label="Photo of hands typing on a laptop" style="background:linear-gradient(135deg,#9fb1c0,#4f5d68)"></div>
    <div class="post-meta">Admin 12/01/2019</div>
    <h3>Rental income</h3>
    <p>It is a long established fact that a reader will be distracted by the readable content of a page</p>
  </article>
  <article class="abs post" style="left:352px;width:244px">
    <div class="post-img" role="img" aria-label="Photo of a desk with paperwork and a laptop" style="background:linear-gradient(135deg,#d8d3cc,#7e7770)"></div>
    <div class="post-meta">Admin 13/01/2019</div>
    <h3>Fermentumal</h3>
    <p>It is a long established fact that a reader will be distracted by the readable content of a page</p>
  </article>
  <article class="abs post post-wide">
    <div class="post-img" role="img" aria-label="Photo of a hand arranging game pieces on a board" style="background:linear-gradient(160deg,#ede6dc,#c9b9a6)"></div>
    <div class="post-body">
      <div class="post-meta">Admin 14/01/2019</div>
      <h3>Plan Rents</h3>
      <p>It is a long established fact that a reader will be distracted by the readable content of a page when looking at its layout.</p>
    </div>
  </article>
  <div class="abs arrow" style="left:1131px"><svg width="20" height="20" viewBox="0 0 20 20"><path d="M7 3l7 7-7 7" fill="none" stroke="#111" stroke-width="3"/></svg></div>
</section>

<footer class="site-footer">
  <div class="abs footer-brand">Meadow Kr Circle</div>
  <p class="abs footer-about">We are a short-term rental management and provides hospitality services to help property owners maximise their rental income.</p>
  <div class="abs footer-col footer-links">
    <h4>LINKS</h4>
    <ul><li>Home</li><li>About Us</li><li>How To Start?</li><li>Package</li><li>Blog</li><li>Testimonial</li><li>Contact Us</li></ul>
  </div>
  <div class="abs footer-col footer-contact">
    <h4>CONTACT &amp; ADDRESS</h4>
    <div class="contact-row first"><svg width="16" height="16" viewBox="0 0 24 24"><path d="M5 3h4l2 5-3 2a12 12 0 0 0 6 6l2-3 5 2v4a2 2 0 0 1-2 2A18 18 0 0 1 3 5a2 2 0 0 1 2-2z" fill="#fff"/></svg>+60 7 555 0182</div>
    <div class="contact-row"><svg width="16" height="14" viewBox="0 0 16 14"><rect x="1" y="1" width="14" height="12" fill="none" stroke="#fff" stroke-width="1.6"/><path d="M1 1l7 6 7-6" fill="none" stroke="#fff" stroke-width="1.6"/></svg>hello@meadowkrcircle.example</div>
    <div class="contact-row"><svg width="14" height="18" viewBox="0 0 20 26"><path d="M10 1a8 8 0 0 0-8 8c0 6 8 15 8 15s8-9 8-15a8 8 0 0 0-8-8z" fill="#fff"/><circle cx="10" cy="9" r="3" fill="#111"/></svg>Unit 12-03 Riverlane Tower, Jalan Seruni,<br>Taman Kenari, 81200.</div>
  </div>
  <div class="abs copyright">Copyright © 2018 - Meadow Kr Circle - All rights reserved.</div>
  <div class="abs social" aria-label="Social links"><span></span><span></span><span></span><span></span></div>
</footer>

</body>
</html>
```